Government contracting small business needs a web design

Tarvex Summit Inc is a veteran owned small business that delivers a full range of professional services as well as training in information technology, security and defense intelligence solutions.
We need a professional/corporate looking website where potential clients can view what services are offered.
This being a new company, there is not much that can added more than a narrative statement, stock photos and a place where potential customers and employees can make contact.
Open to ideas.
Target Market(s)
US Government
Industry/Entity Type
Small Business
Look and feel
Each slider illustrates characteristics of the customer's brand and the style your logo design should communicate.

```html
<!DOCTYPE html>
<html lang="en">
<head>
<meta charset="utf-8">
<title>Tarvex Summit Inc – IT security and intelligence solutions</title>
<link rel="stylesheet" href="https://fonts.googleapis.com/css2?family=Arimo:wght@400&family=PT+Sans:ital,wght@0,400;0,700;1,400&display=swap">
<style>
  :root {
    --page-bg: #2a2a2a;
    --page-bg-line: #2f2f2f;
    --gold: #c2872b;
    --gold-light: #dba83c;
    --gold-dark: #b57a24;
    --gold-active: #d5a331;
    --heading: #c0862b;
    --slider-title: #d6a22a;
    --ink: #2a2a2a;
    --body-text: #5a5a5a;
    --panel: #333333;
    --panel-border: #7a7a7a;
    --panel-text: #f0f0f0;
    --white: #ffffff;
    --band-top: #f7f7f7;
    --band-bottom: #e6e6e6;
    --footer-text: #b9b9b9;
    --social: #3b6aa0;
  }
  * { margin: 0; padding: 0; box-sizing: border-box; }
  html, body { width: 1145px; height: 1200px; overflow: hidden; }
  body {
    background: var(--page-bg);
    background-image: repeating-linear-gradient(45deg, var(--page-bg) 0 3px, var(--page-bg-line) 3px 4px);
    font-family: "PT Sans", Arial, sans-serif;
  }
  .stage {
    position: relative;
    width: 1050px; height: 1100px;
    transform: scale(1.0905, 1.0909);
    transform-origin: 0 0;
  }
  .abs { position: absolute; }

  /* header */
  .search {
    left: 857px; top: 24px; width: 150px; height: 24px;
    background: var(--white); border: 1px solid #cfcfcf; border-radius: 3px;
    font: italic 11px "PT Sans", sans-serif; color: #a8a8a8; padding: 5px 14px;
  }
  .search svg { position: absolute; right: 6px; top: 6px; }
  .nav-band {
    left: 35px; top: 67px; width: 980px; height: 66px;
    background: linear-gradient(var(--gold-light), var(--gold-dark));
    border-radius: 3px 3px 0 0;
  }
  .nav { left: 410px; top: 67px; height: 66px; display: flex; list-style: none; }
  .nav li {
    height: 66px; line-height: 66px; padding: 0 19px;
    font-size: 14px; color: var(--ink);
  }
  .nav li.active { background: var(--gold-active); }
  .logo-box {
    left: 46px; top: 29px; width: 331px; height: 68px;
    background: var(--white); border-radius: 3px;
    box-shadow: 0 2px 5px rgba(0,0,0,.35);
    display: flex; align-items: center; padding-left: 28px; gap: 12px;
  }
  .logo-mark { width: 44px; height: 44px; border-radius: 50%; background: var(--gold); }
  .logo-name { font: 700 31px "PT Sans", sans-serif; color: #4a4a4a; }
  .tagline { left: 46px; top: 106px; width: 416px; text-align: center; font-size: 13px; color: var(--ink); }

  /* content */
  .content { left: 35px; top: 133px; width: 980px; height: 903px; background: var(--white); border-radius: 0 0 3px 3px; }
  .slider-band {
    left: 35px; top: 133px; width: 980px; height: 295px;
    background: linear-gradient(var(--band-top), var(--band-bottom));
    border-bottom: 2px solid #d8d8d8;
  }
  .slider-frame {
    left: 114px; top: 150px; width: 824px; height: 317px;
    background: var(--white); border: 1px solid #cfcfcf;
    box-shadow: 0 14px 14px -10px rgba(0,0,0,.45);
  }
  .slide {
    left: 125px; top: 161px; width: 802px; height: 295px;
    background: linear-gradient(#1d1d1d, #3e3e3e);
    color: #dedede; font-family: Arimo, Arial, sans-serif;
  }
  .slide-art {
    position: absolute; left: 420px; top: 0; width: 382px; height: 295px;
    background: radial-gradient(circle at 55% 40%, #7d8a80 0, #3a4a3c 30%, rgba(40,60,40,.4) 55%, rgba(30,30,30,0) 75%);
  }
  .slide h2 { position: absolute; left: 65px; top: 58px; font: 400 27px Arimo, sans-serif; color: var(--slider-title); }
  .slide p { position: absolute; left: 68px; top: 104px; width: 370px; font-size: 13px; line-height: 20px; }
  .slide ul { position: absolute; left: 75px; top: 162px; width: 340px; list-style: none; display: grid; grid-template-columns: 186px 186px; row-gap: 23px; font-size: 13px; }
  .slide li::before { content: "›"; margin-right: 7px; font-weight: 700; }
  .arrow { top: 292px; }

  /* side panels */
  .panel { left: 45px; width: 260px; background: var(--panel); border: 2px solid var(--panel-border); }
  .tab {
    left: 62px; width: 188px; height: 40px;
    background: var(--gold); border-radius: 3px;
    box-shadow: 0 2px 3px rgba(0,0,0,.3);
    display: flex; align-items: center; gap: 10px; padding-left: 8px;
    font: 700 16px "PT Sans", sans-serif; color: var(--white);
  }
  .tab-icon { width: 30px; height: 26px; border-radius: 3px; background: #e8dcc3; }
  .news-list { list-style: none; padding: 38px 10px 0 20px; color: var(--panel-text); font-size: 11.5px; line-height: 17px; }
  .news-list li { margin-bottom: 19px; }
  .news-list em { display: block; margin-bottom: 5px; }
  .news-list em::before { content: "›"; font-style: normal; font-weight: 700; margin: 0 9px 0 -16px; }
  .news-list span { display: block; padding-left: 16px; }
  .field-label { font-size: 13px; color: var(--white); }
  .field { width: 129px; height: 22px; background: var(--white); border: 1px solid #999; }
  .login-btn {
    left: 213px; top: 878px; width: 60px; height: 23px; border-radius: 3px;
    background: linear-gradient(var(--gold-light), var(--gold-dark));
    color: var(--white); font: 700 12px "PT Sans", sans-serif; text-align: center; line-height: 23px;
  }
  .connect { left: 64px; top: 941px; font-size: 13.5px; font-weight: 700; color: var(--ink); }
  .social { top: 969px; width: 27px; height: 27px; background: var(--social); border-radius: 2px; }

  /* main text */
  .heading { left: 346px; font: 700 16px "PT Sans", sans-serif; color: var(--heading); }
  .copy { left: 343px; font-size: 12.5px; line-height: 20px; color: var(--body-text); text-align: justify; }
  .services { left: 343px; top: 850px; list-style: none; font-size: 12.5px; color: var(--body-text); }
  .services li { height: 28px; }
  .services li span { border-bottom: 1px solid #777; }
  .photo {
    left: 764px; top: 789px; width: 220px; height: 203px; border-radius: 4px; border: 1px solid #bbb;
    background: linear-gradient(135deg, #c9d6ea 0%, #4f6c9c 35%, #1b2a4a 70%, #0c1424 100%);
  }

  /* footer */
  .footer { top: 1062px; font-size: 11px; color: var(--footer-text); }
  .footer-nav { left: 45px; }
  .footer-nav span { padding: 0 4px; }
  .copyright { left: 600px; width: 405px; text-align: right; }
</style>
</head>
<body>
<div class="stage">

  <div class="abs search">Search
    <svg width="11" height="11" viewBox="0 0 11 11"><circle cx="4.5" cy="4.5" r="3.3" fill="none" stroke="#b0b0b0" stroke-width="1.3"/><line x1="7" y1="7" x2="10" y2="10" stroke="#b0b0b0" stroke-width="1.5"/></svg>
  </div>

  <div class="abs nav-band"></div>
  <ul class="abs nav">
    <li class="active">Home</li><li>About Us</li><li>Customers</li><li>Solutions</li><li>News</li><li>Careers</li><li>Contact Us</li>
  </ul>

  <div class="abs logo-box"><div class="logo-mark"></div><div class="logo-name">Tarvex Summit</div></div>
  <div class="abs tagline">IT security and intelligence solutions</div>

  <div class="abs content"></div>
  <div class="abs slider-band"></div>

  <svg class="abs arrow" style="left:61px" width="30" height="32" viewBox="0 0 30 32"><path d="M28 2 L10 16 L28 30 L20 30 L2 16 L20 2 Z" fill="#6a6a6a"/></svg>
  <svg class="abs arrow" style="left:960px" width="30" height="32" viewBox="0 0 30 32"><path d="M2 2 L20 16 L2 30 L10 30 L28 16 L10 2 Z" fill="#6a6a6a"/></svg>

  <div class="abs slider-frame"></div>
  <div class="abs slide">
    <div class="slide-art" role="img" aria-label="Globe ringed with green binary code beside a padlock, symbolising IT security"></div>
    <h2>IT Security....</h2>
    <p>Excepteur sint occaecat cupidatat non proident, sunt in culpa qui officia deserunt mollit anim id est laborum</p>
    <ul>
      <li>Pellentesque vel</li><li>Proin hendrerit eros</li>
      <li>Nam ornare justo</li><li>Nulla vitae semat</li>
    </ul>
  </div>

  <div class="abs panel" style="top:530px;height:198px">
    <ul class="news-list">
      <li><em>Nemo enim ipsam voluptatem</em><span>Voluptas sit aspernatur aut odit aut fugit, sed quia consequuntur magni</span></li>
      <li><em>Nemo enim ipsam voluptatem</em><span>Voluptas sit aspernatur aut odit aut fugit, sed quia consequuntur magni</span></li>
    </ul>
  </div>
  <div class="abs tab" style="top:508px"><div class="tab-icon"></div>Latets News</div>

  <div class="abs panel" style="top:759px;height:168px"></div>
  <div class="abs tab" style="top:737px"><div class="tab-icon"></div>Client Login</div>
  <div class="abs field-label" style="left:67px;top:799px">User name :</div>
  <div class="abs field" style="left:144px;top:798px"></div>
  <div class="abs field-label" style="left:71px;top:842px">Pass word :</div>
  <div class="abs field" style="left:144px;top:840px"></div>
  <div class="abs login-btn">LOG IN</div>

  <div class="abs connect">Connect with us</div>
  <div class="abs social" style="left:89px"></div>
  <div class="abs social" style="left:128px"></div>
  <div class="abs social" style="left:167px"></div>
  <div class="abs social" style="left:207px"></div>

  <h3 class="abs heading" style="top:507px">Welcome to our site</h3>
  <p class="abs copy" style="top:545px;width:640px">Consectetur adipisicing elit, sed do eiusmod tempor incididunt ut labore et dolore magna aliqua. Ut enim ad minim veniam, quis nostrud exercitation ullamco laboris nisi ut aliquip ex ea commodo consequat. Duis aute irure dolor in reprehenderit in voluptate velit esse cillum dolore eu fugiat nulla pariatur. Excepteur sint occaecat cupidatat non proident, sunt in culpa qui officia deserunt mollit anim id est laborum. Sed ut perspiciatis unde omnis iste natus error sit voluptatem accusantium doloremque laudantium, totam rem aperiam, eaque ipsa quae ab illo inventore veritatis et quasi architecto beatae vitae dicta sunt explicabo. Nemo enim ipsam voluptatem quia voluptas sit aspernatur aut odit aut fugit, sed quia consequuntur magni dolores eos qui ratione voluptatem</p>

  <h3 class="abs heading" style="top:739px">Our Services</h3>
  <p class="abs copy" style="top:777px;width:410px;text-align:left">Consectetur adipisicing elit, sed do eiusmod tempor incididunt ut labore et dolore magna aliqua. Ut enim ad minim veniam, quis nostrud exercitation ullamco laboris nisi ut aliquip ex ea commodo consequat</p>
  <ul class="abs services">
    <li><span>Pellentesque vel mauris vel nisl pulvinar rhoncus.</span></li>
    <li><span>Proin hendrerit eros nec magna placerat sodales.</span></li>
    <li><span>Nulla vitae sem at risus pellentesque fringilla.</span></li>
    <li><span>Suspendisse non felis vel nunc adipiscing facilisis.</span></li>
    <li><span>Proin hendrerit eros nec magna placerat sodales.</span></li>
    <li><span>Nulla vitae sem at risus pellentesque fringilla.</span></li>
  </ul>
  <div class="abs photo" role="img" aria-label="Rows of computer workstations in a blue-lit office"></div>

  <div class="abs footer footer-nav">Home<span>|</span>About Us<span>|</span>Customers<span>|</span>Solutions<span>|</span>News<span>|</span>Careers<span>|</span>Contact Us<span>|</span>Sitemap</div>
  <div class="abs footer copyright">Copyright © 2012 www.tarvexsummit.com &nbsp; All rights reserved</div>

</div>
</body>
</html>
```